Garlic Farm for Farm Sales/Restaurant sales

Need a professional, but appealing to agriculture world. We are selling 27 kinds of Organic Garlic from a farm in Simla,CO. I have uploaded logo and business information-we are going to need a template, because I will need to use it for four separate people.
-We are trying to appeal to Farm to table restaurants
-As well as growers/farmers

Target Market(s)

Agriculture Sales/Restaurants-Organic

Industry/Entity Type

Agriculture

Contact Information for Business Card

Want it to look more unique then your average kelto stock card- I want it to look amazing

Font styles to use
Sans Serif

Colors
0455a3
ec1f27
fbed22
ffffff

Requirements
Must have
• Just be creative
Nice to have
• Colorful
Should not have
• plain

```html
<!DOCTYPE html>
<html lang="en">
<head>
<meta charset="utf-8">
<title>Prairie Clove Garlic – Business Card</title>
<link rel="stylesheet" href="https://fonts.googleapis.com/css2?family=Open+Sans:wght@400;700&display=swap">
<style>
  :root {
    --navy: #0b2c63;
    --navy-deep: #1a2e5c;
    --red: #c0092d;
    --white: #ffffff;
    --paper: #f2f2f2;
    --backdrop: #dcdcdc;
    --shadow: rgba(0, 0, 0, 0.22);
  }
  * { box-sizing: border-box; margin: 0; padding: 0; }
  html, body {
    width: 1200px;
    height: 900px;
    overflow: hidden;
    background: var(--backdrop);
    font-family: "Open Sans", Arial, sans-serif;
  }
  .canvas {
    position: relative;
    width: 1200px;
    height: 900px;
  }
  .card {
    position: absolute;
    left: 290px;
    width: 620px;
    height: 354px;
    overflow: hidden;
    box-shadow: 0 6px 18px var(--shadow);
  }
  .card-back { top: 76px; background: var(--navy); }
  .card-front { top: 470px; background: var(--paper); }

  .card-shapes { position: absolute; inset: 0; }

  /* brand lockup */
  .brand {
    position: absolute;
    display: flex;
    align-items: center;
    font-weight: 700;
    text-transform: lowercase;
    letter-spacing: 0.5px;
  }
  .brand-dot { border-radius: 50%; flex: none; }
  .card-back .brand {
    left: 0; right: 0; top: 150px;
    justify-content: center;
    gap: 12px;
    color: var(--white);
    font-size: 38px;
  }
  .card-back .brand-dot { width: 30px; height: 30px; background: var(--white); }
  .card-front .brand {
    left: 30px; top: 104px;
    width: 220px;
    flex-direction: column;
    gap: 10px;
    text-align: center;
    color: var(--navy-deep);
    font-size: 26px;
    line-height: 1.1;
  }
  .card-front .brand-dot { width: 40px; height: 40px; background: var(--red); }

  /* contact block */
  .contact {
    position: absolute;
    right: 26px;
    top: 46px;
    text-align: right;
    color: var(--white);
  }
  .person-name {
    font-size: 27px;
    font-weight: 700;
    text-transform: lowercase;
    line-height: 1.1;
  }
  .person-role { font-size: 17px; line-height: 1.3; }
  .address { margin-top: 28px; font-size: 15px; line-height: 1.35; }
  .lines { margin-top: 20px; list-style: none; font-size: 15px; line-height: 1.45; }
  .lines li { display: flex; justify-content: flex-end; align-items: center; gap: 8px; }
  .lines svg { width: 13px; height: 13px; flex: none; }
</style>
</head>
<body>
<main class="canvas">

  <section class="card card-back" aria-label="Business card back">
    <div class="brand">
      <span class="brand-dot"></span>
      <span class="brand-name">prairie clove garlic</span>
    </div>
  </section>

  <section class="card card-front" aria-label="Business card front">
    <svg class="card-shapes" viewBox="0 0 620 354" preserveAspectRatio="none" aria-hidden="true">
      <path d="M282 0 Q338 190 176 354 L620 354 L620 0 Z" fill="var(--red)"/>
      <path d="M266 0 Q326 196 150 354 L176 354 Q338 190 282 0 Z" fill="var(--navy-deep)"/>
      <path d="M286 0 Q344 190 182 354 L186 354 Q348 190 290 0 Z" fill="var(--white)" opacity="0.85"/>
    </svg>

    <div class="brand">
      <span class="brand-dot"></span>
      <span class="brand-name">prairie clove<br>garlic</span>
    </div>

    <div class="contact">
      <p class="person-name">dana reyes</p>
      <p class="person-role">Owner</p>
      <p class="address">PO Box 218307,<br>Limon, CO 80828</p>
      <ul class="lines">
        <li>719-408-2261
          <svg viewBox="0 0 16 16" aria-hidden="true"><path fill="var(--white)" d="M3 2h3l1.5 3.5-2 1.2a8 8 0 0 0 3.8 3.8l1.2-2L14 10v3a1.5 1.5 0 0 1-1.5 1.5A11 11 0 0 1 1.5 3.5 1.5 1.5 0 0 1 3 2z"/></svg>
        </li>
        <li>(719)-552-7
          <svg viewBox="0 0 16 16" aria-hidden="true"><rect x="4" y="1" width="8" height="14" rx="1.5" fill="var(--white)"/><rect x="5.5" y="3" width="5" height="8" fill="var(--red)"/></svg>
        </li>
        <li>hello@prairieclove.com
          <svg viewBox="0 0 16 16" aria-hidden="true"><rect x="1" y="3" width="14" height="10" fill="var(--white)"/><path d="M1 3l7 6 7-6" fill="none" stroke="var(--red)" stroke-width="1.3"/></svg>
        </li>
        <li>www.prairieclove.com
          <svg viewBox="0 0 16 16" aria-hidden="true"><circle cx="8" cy="8" r="7" fill="var(--white)"/><path d="M1 8h14M8 1c-3 3-3 11 0 14M8 1c3 3 3 11 0 14" fill="none" stroke="var(--red)" stroke-width="1.1"/></svg>
        </li>
      </ul>
    </div>
  </section>

</main>
</body>
</html>
```